Quorindel Business Cards & Stationery Design
Business Cards & Stationery Design
Quorindel Business Cards & Stationery Design - Information Technology
Creative Brief
Professional
Dennis Holbrook
Technical Consultant
47 marigold lane coventry NSW 2012 Australia
dholbrook@quorindel.com
http://www.quorindel.com
The font used is called Aller, and can be downloaded from : http://www.fentrowtype.com/buyonline/fonts/aller
www.quorindel.com

```html
<!DOCTYPE html>
<html lang="en">
<head>
<meta charset="utf-8">
<title>Quorindel Stationery Set</title>
<link href="https://fonts.googleapis.com/css2?family=Open+Sans:wght@400;600&display=swap" rel="stylesheet">
<style>
:root{
  --bg:#3a3a3a;
  --paper:#ffffff;
  --paper-shade:#eeeeee;
  --ink:#2a2a2a;
  --muted:#8a8a8a;
  --green:#3c8c2f;
  --flap-dark:#1e1e1e;
  --flap-grey:#8c8c8c;
  --watermark:#e6e6e6;
}
*{margin:0;padding:0;box-sizing:border-box}
html,body{width:1200px;height:338px;overflow:hidden}
body{background:var(--bg);font-family:"Open Sans",sans-serif;color:var(--ink);position:relative}
.item{position:absolute;background:var(--paper);box-shadow:0 2px 6px rgba(0,0,0,.45)}
.label{position:absolute;font-size:5px;color:#cfcfcf;white-space:nowrap}
.brand{display:flex;align-items:center;gap:3px;font-weight:600;color:var(--green);line-height:1}
.brand .dot{background:var(--green);display:inline-block}
.watermark{position:absolute;background:var(--watermark)}
.small{font-size:3.5px;color:var(--muted);line-height:1.5}
.footer-label{position:absolute;bottom:4px;left:0;right:0;text-align:center;font-size:3.5px;color:var(--muted)}

/* business cards */
.card{left:29px;width:110px;height:50px}
.card-front{top:125px}
.card-back{top:197px}
.card-front .brand{position:absolute;left:8px;top:18px;font-size:10px}
.card-front .brand .dot{width:6px;height:6px}
.card-back .person{position:absolute;left:8px;top:8px;font-size:5px;font-weight:600}
.card-back .role{position:absolute;left:8px;top:15px;font-size:3.5px;color:var(--muted)}
.card-back .small{position:absolute;left:8px;bottom:6px}

/* letterheads */
.letter{top:14px;width:160px;height:315px}
.letter-one{left:154px}
.letter-two{left:334px}
.letter .brand{position:absolute;left:56px;top:24px;font-size:11px}
.letter .brand .dot{width:7px;height:7px}
.letter-one .watermark{left:50px;top:170px;width:60px;height:60px}
.letter-two .watermark{left:45px;top:130px;width:70px;height:70px}
.letter-one .side{position:absolute;left:10px;bottom:26px}

/* envelopes front */
.envelope{left:629px;width:266px;height:116px}
.envelope-one{top:43px}
.envelope-two{top:182px}
.envelope .brand{position:absolute;left:12px;top:16px;font-size:11px}
.envelope .brand .dot{width:7px;height:7px}
.envelope .small{position:absolute;left:12px;top:34px}
.envelope .watermark{right:30px;bottom:10px;width:44px;height:44px}

/* envelopes back */
.env-back{left:912px;width:278px;overflow:hidden}
.env-back-dark{top:12px;height:130px}
.env-back-grey{top:158px;height:164px}
.env-back svg{position:absolute;left:0;top:0}
.env-back .centre{position:absolute;left:131px;width:16px;height:16px;background:var(--paper);border:1px solid var(--green)}
.env-back-dark .centre{top:30px}
.env-back-grey .centre{top:44px}
</style>
</head>
<body>

<span class="label" style="left:29px;top:117px">Business Card Front</span>
<div class="item card card-front">
  <div class="brand"><span class="dot"></span>quorindel</div>
</div>

<span class="label" style="left:29px;top:189px">Business Card Back</span>
<div class="item card card-back">
  <div class="person">Dennis Holbrook</div>
  <div class="role">Technical Consultant</div>
  <div class="small">47 marigold lane coventry NSW 2012 Australia<br>dholbrook@quorindel.com<br>www.quorindel.com</div>
</div>

<div class="item letter letter-one">
  <div class="brand"><span class="dot"></span>quorindel</div>
  <div class="watermark"></div>
  <div class="small side">47 marigold lane<br>coventry NSW 2012<br>Australia<br>www.quorindel.com</div>
  <div class="footer-label">Letterhead Page One</div>
</div>

<div class="item letter letter-two">
  <div class="brand"><span class="dot"></span>quorindel</div>
  <div class="watermark"></div>
  <div class="footer-label">Letterhead Page Two</div>
</div>

<div class="item envelope envelope-one">
  <div class="brand"><span class="dot"></span>quorindel</div>
  <div class="small">www.quorindel.com</div>
  <div class="watermark"></div>
  <div class="footer-label">Envelope Front One</div>
</div>

<div class="item envelope envelope-two">
  <div class="brand"><span class="dot"></span>quorindel</div>
  <div class="small">www.quorindel.com</div>
  <div class="watermark"></div>
  <div class="footer-label">Envelope Front Two</div>
</div>

<div class="item env-back env-back-dark">
  <svg width="278" height="130" viewBox="0 0 278 130">
    <polygon points="0,130 139,60 278,130" fill="var(--paper-shade)"/>
    <path d="M0,0 H278 V18 Q139,90 0,18 Z" fill="var(--flap-dark)"/>
  </svg>
  <div class="centre"></div>
</div>

<div class="item env-back env-back-grey">
  <svg width="278" height="164" viewBox="0 0 278 164">
    <polygon points="0,164 139,76 278,164" fill="var(--paper-shade)"/>
    <path d="M0,0 H278 V22 Q139,100 0,22 Z" fill="var(--flap-grey)"/>
  </svg>
  <div class="centre"></div>
  <div class="footer-label">Envelope Back View</div>
</div>

</body>
</html>
```